Create American style design suitable for consumers in Europe and America

We need a professional universal neutral design, which can be applied to all personal care tools, regardless of male and female, and the color matching needs to be matched by designers themselves.
Updates

设计质量低

Target Market(s)

Europe and America

Industry/Entity Type

personal care tools

Font styles to use
Serif
Sans Serif
Script

Requirements
Must have
• personal beauty care tool,like nail clipper,tweezer,scissors
Nice to have
• The copywriter plans on the packaging design can be applied to all personal care tools
Should not have
• Not designed for a single product, but for a whole personal care tool

```html
<!DOCTYPE html>
<html lang="en">
<head>
<meta charset="utf-8">
<title>lumo Groom Care – Packaging Board</title>
<link href="https://fonts.googleapis.com/css2?family=Archivo+Black&family=Montserrat:wght@300;400;600&family=Great+Vibes&display=swap" rel="stylesheet">
<style>
  :root{
    --sky:#a6d0ea; --royal:#101f8a;
    --forest:#0d5a3c; --mint:#97d68a;
    --midnight:#24284f; --mist:#dfe9e8;
    --paper:#ffffff; --cut:#d63fb0; --ink:#222;
    --stage:#eceeee; --stage-dark:#a9adab;
  }
  html,body{margin:0;padding:0;width:1200px;height:977px;overflow:hidden;background:var(--paper);}
  .board{position:relative;width:1200px;height:977px;font-family:"Montserrat",sans-serif;}
  .section-title{position:absolute;left:20px;margin:0;font-family:"Archivo Black",sans-serif;font-size:19px;letter-spacing:1.5px;color:var(--ink);font-weight:400;}
  .title-box{top:24px}.title-label{top:408px}.title-mock{top:566px}
  .art{position:absolute;left:0;top:0;width:1200px;height:977px}
  .dk{fill:var(--dk)} .lt{fill:var(--lt)} .wh{fill:var(--paper)}
  .cut{fill:none;stroke:var(--cut);stroke-width:1}
  .logo{font-family:"Montserrat",sans-serif;font-weight:300;font-size:24px;letter-spacing:-0.5px}
  .logo-sub{font-family:"Montserrat",sans-serif;font-size:6px}
  .headline{font-family:"Montserrat",sans-serif;font-weight:600;font-size:19px;fill:var(--dk)}
  .body{font-family:"Montserrat",sans-serif;font-size:5px;fill:var(--dk)}
  .script{font-family:"Great Vibes",cursive;font-size:16px;fill:var(--dk)}
  .t-dk{fill:var(--dk)} .t-wh{fill:var(--paper)} .t-lt{fill:var(--lt)}
  .photo{fill:url(#photoTone)}
  .chip-code{font-family:"Montserrat",sans-serif;font-size:9px;fill:var(--ink)}
  .trend{font-family:"Archivo Black",sans-serif;font-size:12px;fill:#555}
  .tag-text{font-family:"Montserrat",sans-serif;font-weight:600;font-size:8px}
  .tag-small{font-family:"Montserrat",sans-serif;font-size:6.5px}
</style>
</head>
<body>
<div class="board">
  <h2 class="section-title title-box">BOX SAMPLES</h2>
  <h2 class="section-title title-label">LABEL SAMPLES</h2>
  <h2 class="section-title title-mock">MOCK UP SAMPLE</h2>

  <svg class="art" viewBox="0 0 2134 1738" xmlns="http://www.w3.org/2000/svg">
    <defs>
      <linearGradient id="photoTone" x1="0" y1="0" x2="1" y2="1">
        <stop offset="0" stop-color="#c9cdcf"/><stop offset="1" stop-color="#7d8386"/>
      </linearGradient>
      <clipPath id="roundTag"><circle cx="0" cy="0" r="75"/></clipPath>
      <clipPath id="roundTagLarge"><circle cx="0" cy="0" r="95"/></clipPath>

      <g id="dieline">
        <path class="lt" d="M80,138 V48 Q80,8 120,8 H292 Q332,8 332,48 V138 Z"/>
        <path class="dk" d="M5,110 Q5,72 40,72 H80 L93,110 V400 L80,437 H40 Q5,437 5,400 Z"/>
        <path class="dk" d="M320,110 L333,72 H365 Q397,72 397,110 V400 Q397,437 365,437 H333 L320,400 Z"/>
        <rect class="lt" x="93" y="138" width="227" height="234"/>
        <rect class="wh" x="242" y="138" width="78" height="234"/>
        <rect class="lt" x="397" y="138" width="228" height="234"/>
        <rect class="wh" x="547" y="138" width="78" height="234"/>
        <polygon class="dk" points="625,138 670,152 670,358 625,372"/>
        <path class="lt" d="M385,372 H635 V462 Q635,502 595,502 H425 Q385,502 385,462 Z"/>
        <rect class="cut" x="93" y="138" width="532" height="234"/>
        <line class="cut" x1="320" y1="138" x2="320" y2="372"/>
        <line class="cut" x1="397" y1="138" x2="397" y2="372"/>
        <path class="cut" d="M93,138 V60 H320 V138"/>
        <path class="cut" d="M397,372 V450 H625 V372"/>
        <path class="cut" d="M18,138 V88 H80 M18,372 V420 H80"/>
        <path class="cut" d="M333,138 V88 H383 M333,372 V420 H383"/>

        <text class="logo t-wh" x="186" y="104" text-anchor="middle">lumo</text>
        <text class="logo-sub t-wh" x="186" y="114" text-anchor="middle">Groom Care</text>

        <text class="logo t-wh" x="32" y="172">lumo</text>
        <text class="logo-sub t-wh" x="32" y="181">Groom Care</text>
        <rect class="photo" role="img" aria-label="Small photo of the care tool" x="30" y="228" width="40" height="60" rx="4"/>
        <text class="body t-wh" x="49" y="310" text-anchor="middle">Lorem ipsum dolor</text>
        <text class="body t-wh" x="49" y="317" text-anchor="middle">sit amet, consec-</text>

        <text class="logo t-dk" x="110" y="172">lumo</text>
        <text class="logo-sub t-dk" x="110" y="181">Groom Care</text>
        <text class="headline" x="110" y="210">Lorem</text>
        <text class="headline" x="110" y="233">ipsum</text>
        <text class="headline" x="110" y="256">dolor sit</text>
        <text class="body" x="110" y="275">Lorem ipsum dolor sit amet</text>
        <text class="body" x="110" y="282">consectetuer adipiscing elit</text>
        <text class="body" x="110" y="289">sed diam nonummy nibh</text>
        <text class="body" x="110" y="296">euismod tincidunt ut laoreet</text>
        <text class="body" x="110" y="303">dolore magna aliquam</text>
        <text class="script" x="110" y="352">Lorem ipsum</text>
        <rect class="photo" role="img" aria-label="Photo of the personal care tool" x="215" y="180" width="100" height="150" rx="8"/>

        <text class="logo t-wh" x="347" y="172">lumo</text>
        <text class="logo-sub t-wh" x="347" y="181">Groom Care</text>
        <rect class="photo" role="img" aria-label="Small photo of the care tool" x="339" y="228" width="40" height="60" rx="4"/>
        <text class="body t-wh" x="358" y="310" text-anchor="middle">Lorem ipsum dolor</text>
        <text class="body t-wh" x="358" y="317" text-anchor="middle">sit amet, consec-</text>

        <text class="logo t-dk" x="413" y="172">lumo</text>
        <text class="logo-sub t-dk" x="413" y="181">Groom Care</text>
        <text class="script" x="515" y="168" style="font-size:12px">Lorem ipsum</text>
        <circle class="wh" cx="490" cy="235" r="42" opacity="0.85"/>
        <rect class="photo" role="img" aria-label="Photo of the care tool on a round plate" x="480" y="195" width="110" height="120" rx="8"/>
        <text class="body" x="420" y="300">• Lorem ipsum dolor sit amet, consectetuer</text>
        <text class="body" x="420" y="307">• Lorem ipsum dolor sit amet, consectetuer</text>
        <text class="body" x="420" y="314">• Lorem ipsum dolor sit amet, consectetuer</text>
        <text class="body" x="420" y="321">• Lorem ipsum dolor sit amet</text>
        <text class="body" x="420" y="350" style="font-weight:600">Lorem ipsum dolor sit amet</text>
        <text class="body" x="420" y="357">adipiscing elit, sed diam</text>
      </g>

      <g id="roundDark">
        <g clip-path="url(#roundTag)">
          <rect class="dk" x="-75" y="-75" width="150" height="150"/>
          <rect class="lt" x="-75" y="5" width="150" height="48"/>
        </g>
        <circle cx="0" cy="-50" r="3" fill="none" stroke="var(--cut)"/>
        <text class="logo t-wh" x="0" y="-15" text-anchor="middle" style="font-size:20px">lumo</text>
        <text class="logo-sub t-wh" x="0" y="-6" text-anchor="middle">Groom Care</text>
        <text class="tag-text t-dk" x="0" y="25" text-anchor="middle">Lorem ipsum dolor sit amet</text>
        <text class="tag-small t-dk" x="0" y="35" text-anchor="middle">adipiscing elit, sed diam</text>
      </g>
      <g id="roundLight">
        <g clip-path="url(#roundTag)">
          <rect class="lt" x="-75" y="-75" width="150" height="150"/>
          <rect class="dk" x="-75" y="5" width="150" height="48"/>
        </g>
        <circle cx="0" cy="0" r="70" fill="none" stroke="var(--cut)"/>
        <circle cx="0" cy="-50" r="3" fill="none" stroke="var(--cut)"/>
        <text class="logo t-wh" x="0" y="-15" text-anchor="middle" style="font-size:20px">lumo</text>
        <text class="logo-sub t-wh" x="0" y="-6" text-anchor="middle">Groom Care</text>
        <text class="tag-text t-wh" x="0" y="25" text-anchor="middle">Lorem ipsum dolor sit amet</text>
        <text class="tag-small t-wh" x="0" y="35" text-anchor="middle">adipiscing elit, sed diam</text>
      </g>
      <g id="rectDark">
        <rect class="dk" x="0" y="0" width="107" height="150"/>
        <rect class="cut" x="5" y="5" width="97" height="140"/>
        <text class="logo t-wh" x="53" y="52" text-anchor="middle" style="font-size:20px">lumo</text>
        <text class="logo-sub t-wh" x="53" y="61" text-anchor="middle">Groom Care</text>
        <text class="tag-small t-wh" x="18" y="84">• Lorem ipsum dolor sit</text>
        <text class="tag-small t-wh" x="18" y="99">• Lorem ipsum dolor sit</text>
        <text class="tag-small t-wh" x="18" y="114">• Lorem ipsum dolor sit</text>
        <text class="tag-text t-wh" x="53" y="130" text-anchor="middle" style="font-size:7px">Lorem ipsum dolor sit</text>
        <text class="tag-small t-wh" x="53" y="138" text-anchor="middle" style="font-size:5px">adipiscing elit, sed diam</text>
      </g>
      <g id="rectLight">
        <rect class="lt" x="0" y="0" width="107" height="150"/>
        <rect class="cut" x="5" y="5" width="97" height="140"/>
        <circle cx="53" cy="14" r="3" fill="none" stroke="var(--cut)"/>
        <text class="logo t-wh" x="53" y="52" text-anchor="middle" style="font-size:20px">lumo</text>
        <text class="logo-sub t-wh" x="53" y="61" text-anchor="middle">Groom Care</text>
        <rect class="dk" x="0" y="92" width="107" height="30"/>
        <text class="tag-text t-wh" x="53" y="106" text-anchor="middle" style="font-size:7px">Lorem ipsum dolor sit</text>
        <text class="tag-small t-wh" x="53" y="115" text-anchor="middle" style="font-size:5px">adipiscing elit, sed diam</text>
      </g>
    </defs>

    <!-- trend palette -->
    <text class="trend" x="1720" y="36">2023/24</text>
    <text class="trend" x="1720" y="50">GLOBAL COLOUR</text>
    <text class="trend" x="1720" y="64">PALETTES BY TREND</text>
    <rect x="1893" y="26" width="24" height="26" fill="var(--sky)"/>
    <rect x="1930" y="26" width="24" height="26" fill="var(--royal)"/>
    <rect x="1967" y="26" width="24" height="26" fill="var(--forest)"/>
    <rect x="2004" y="26" width="24" height="26" fill="var(--mint)"/>
    <rect x="2041" y="26" width="24" height="26" fill="var(--midnight)"/>
    <rect x="2078" y="26" width="24" height="26" fill="var(--mist)"/>

    <!-- box dielines -->
    <g style="--dk:var(--royal);--lt:var(--sky)"><use href="#dieline" x="30" y="120"/></g>
    <g style="--dk:var(--forest);--lt:var(--mint)"><use href="#dieline" x="715" y="120"/></g>
    <g style="--dk:var(--midnight);--lt:var(--mist)"><use href="#dieline" x="1425" y="120"/></g>

    <!-- colour chips -->
    <rect x="45" y="595" width="35" height="36" fill="var(--sky)"/><text class="chip-code" x="45" y="648">14-4123</text>
    <rect x="107" y="595" width="35" height="36" fill="var(--royal)"/><text class="chip-code" x="107" y="648">19-3953</text>
    <rect x="730" y="592" width="37" height="38" fill="var(--forest)"/><text class="chip-code" x="730" y="648">330</text>
    <rect x="790" y="592" width="37" height="38" fill="var(--mint)"/><text class="chip-code" x="790" y="648">15-6317</text>
    <rect x="1440" y="592" width="37" height="38" fill="var(--midnight)"/><text class="chip-code" x="1440" y="648">19-3932</text>
    <rect x="1500" y="592" width="37" height="38" fill="var(--mist)"/><text class="chip-code" x="1500" y="648">7541c</text>

    <!-- labels -->
    <g style="--dk:var(--royal);--lt:var(--sky)">
      <use href="#roundDark" x="124" y="875"/>
      <use href="#roundLight" x="290" y="875"/>
      <use href="#rectDark" x="428" y="800"/>
      <use href="#rectLight" x="545" y="800"/>
    </g>
    <g style="--dk:var(--forest);--lt:var(--mint)">
      <use href="#roundDark" x="818" y="875"/>
      <use href="#roundLight" x="984" y="875"/>
      <use href="#rectDark" x="1122" y="800"/>
      <use href="#rectLight" x="1239" y="800"/>
    </g>
    <g style="--dk:var(--midnight);--lt:var(--mist)">
      <use href="#roundDark" x="1530" y="875"/>
      <use href="#roundLight" x="1696" y="875"/>
      <use href="#rectDark" x="1833" y="800"/>
      <use href="#rectLight" x="1952" y="800"/>
    </g>

    <!-- mock up, shown flat -->
    <g style="--dk:var(--royal);--lt:var(--sky)">
      <rect x="38" y="1078" width="822" height="600" fill="var(--stage)"/>
      <rect class="lt" x="205" y="1160" width="230" height="480"/>
      <rect class="wh" x="435" y="1160" width="130" height="480"/>
      <rect class="dk" x="565" y="1160" width="75" height="480"/>
      <text class="logo t-dk" x="225" y="1222" style="font-size:36px">lumo</text>
      <text class="logo-sub t-dk" x="227" y="1236" style="font-size:10px">Groom Care</text>
      <text class="script" x="385" y="1215" style="font-size:26px">Lorem ipsum</text>
      <circle class="wh" cx="345" cy="1345" r="68" opacity="0.85"/>
      <rect class="photo" role="img" aria-label="Photo of an eyelash curler" x="340" y="1300" width="190" height="200" rx="10"/>
      <text class="body" x="228" y="1468" style="font-size:9px">• Lorem ipsum do</text>
      <text class="body" x="228" y="1482" style="font-size:9px">• Lorem ipsum dolor sit amet, consectetuer</text>
      <text class="body" x="228" y="1496" style="font-size:9px">• Lorem ipsum dolor sit amet, consectetuer</text>
      <text class="body" x="228" y="1510" style="font-size:9px">• Lorem ipsum dolor sit amet, consectetuer</text>
      <text class="body" x="228" y="1524" style="font-size:9px">lor sit amet, consectetuer</text>
      <text class="body" x="226" y="1572" style="font-size:10px;font-weight:600">Lorem ipsum dolor sit amet</text>
      <text class="body" x="226" y="1586" style="font-size:9px">adipiscing elit, sed diam</text>
      <text class="logo t-wh" x="585" y="1220" style="font-size:26px">lumo</text>
      <text class="logo-sub t-wh" x="587" y="1232" style="font-size:8px">Groom Care</text>
      <rect class="photo" role="img" aria-label="Small photo of an eyelash curler" x="585" y="1340" width="36" height="90" rx="4"/>
      <text class="body t-wh" x="602" y="1480" text-anchor="middle" style="font-size:7px">Lorem ipsum dolor</text>
      <text class="body t-wh" x="602" y="1490" text-anchor="middle" style="font-size:7px">sit amet, consec-</text>

      <rect x="862" y="1078" width="822" height="600" fill="var(--stage)"/>
      <rect class="lt" x="1030" y="1160" width="230" height="480"/>
      <rect class="wh" x="1260" y="1160" width="130" height="480"/>
      <rect class="dk" x="1390" y="1160" width="75" height="480"/>
      <text class="logo t-dk" x="1055" y="1225" style="font-size:36px">lumo</text>
      <text class="logo-sub t-dk" x="1057" y="1239" style="font-size:10px">Groom Care</text>
      <text class="headline" x="1055" y="1300" style="font-size:32px">Lorem</text>
      <text class="headline" x="1055" y="1344" style="font-size:32px">ipsum</text>
      <text class="headline" x="1055" y="1388" style="font-size:32px">dolor sit</text>
      <text class="body" x="1055" y="1420" style="font-size:9px">Lorem ipsum dolor sit</text>
      <text class="body" x="1055" y="1433" style="font-size:9px">amet, consectetuer adipi-</text>
      <text class="body" x="1055" y="1446" style="font-size:9px">scing elit, sed diam</text>
      <text class="body" x="1055" y="1459" style="font-size:9px">nonummy nibh euismod</text>
      <text class="body" x="1055" y="1472" style="font-size:9px">tincidunt ut laoreet</text>
      <text class="body" x="1055" y="1485" style="font-size:9px">dolore magna aliquam</text>
      <text class="body" x="1055" y="1498" style="font-size:9px">erat volutpat. Ut wisi</text>
      <text class="body" x="1055" y="1511" style="font-size:9px">enim ad minim</text>
      <text class="script" x="1055" y="1570" style="font-size:26px">Lorem ipsum</text>
      <rect class="photo" role="img" aria-label="Photo of an eyelash curler" x="1205" y="1270" width="140" height="290" rx="10"/>
      <text class="logo t-wh" x="1410" y="1222" style="font-size:26px">lumo</text>
      <text class="logo-sub t-wh" x="1412" y="1234" style="font-size:8px">Groom Care</text>
      <rect class="photo" role="img" aria-label="Small photo of an eyelash curler" x="1410" y="1340" width="36" height="90" rx="4"/>
      <text class="body t-wh" x="1427" y="1480" text-anchor="middle" style="font-size:7px">Lorem ipsum dolor</text>
      <text class="body t-wh" x="1427" y="1490" text-anchor="middle" style="font-size:7px">sit amet, consec-</text>

      <rect x="1685" y="1078" width="369" height="300" fill="var(--stage-dark)"/>
      <use href="#rectDark" x="1775" y="1165"/>
      <use href="#rectLight" x="1850" y="1190"/>
      <rect x="1685" y="1378" width="369" height="300" fill="var(--stage)"/>
      <g transform="translate(1865,1555)">
        <g clip-path="url(#roundTagLarge)">
          <rect class="dk" x="-95" y="-95" width="190" height="190"/>
          <rect class="lt" x="-95" y="-20" width="190" height="50"/>
        </g>
        <text class="logo t-wh" x="0" y="-40" text-anchor="middle" style="font-size:26px">lumo</text>
        <text class="logo-sub t-wh" x="0" y="-28" text-anchor="middle" style="font-size:8px">Groom Care</text>
        <text class="tag-text t-dk" x="0" y="3" text-anchor="middle" style="font-size:10px">Lorem ipsum dolor sit amet</text>
        <text class="tag-small t-dk" x="0" y="16" text-anchor="middle" style="font-size:8px">adipiscing elit, sed diam</text>
      </g>
    </g>
  </svg>
</div>
</body>
</html>
```